Business Card Design: recruitment/consultancy for business Thrive360onward

We need a business card design for a new company based in Adelaide Australia called Thrive360onward. Our Business aims to support people over 50 who may be looking for a career change, have been made redundant or generally looking for employment. We will also be working with businesses to provide them with recruiting solutions, job design, recruitment strategies and customised training. we will also be working with volunteering opportunities for those over 50.
We would like to see the E in thrive360onward strong and dominant. The final design should reflect change for the better, better opportunities, today is the day, make way for the new, all aimed at the 50 plus age group.
Colours we are thinking off include green (money, growth) black and white.... we like the idea of black and white photography with a one dominant colour...think of a of a black and white photo of a woman with dominant red lips...that sort of look

Business

Contact Information for Business Card

Kim, Mavis & Gwen
phone: 0439615028
Thrive360onward@mailbox-example.net
Facebook/Thrive360onward
www.thrive360onward-example.com.au

```html
<!DOCTYPE html>
<html lang="en">
<head>
<meta charset="utf-8">
<title>Thrive360onward business cards</title>
<link rel="stylesheet" href="https://fonts.googleapis.com/css2?family=Roboto:wght@300;400&family=Kalam:wght@400&display=swap">
<style>
  :root {
    --backdrop: #e9e6e2;
    --card-white: #ffffff;
    --card-dark: #1f1416;
    --card-dark-edge: #2c1e21;
    --ink: #1a1a1a;
    --text-light: #f4f0f0;
    --accent-red: #e0393e;
  }
  * { box-sizing: border-box; margin: 0; padding: 0; }
  html, body { width: 1200px; height: 858px; overflow: hidden; }
  body {
    background: var(--backdrop);
    font-family: "Roboto", Arial, sans-serif;
    font-weight: 300;
    position: relative;
  }
  .card {
    position: absolute;
    top: 275px;
    width: 540px;
    height: 309px;
    border-radius: 3px;
    overflow: hidden;
    box-shadow: 0 6px 18px rgba(0,0,0,0.18);
  }
  /* Contact side */
  .card--contact { left: 40px; background: var(--card-white); }
  .contact__portrait-panel {
    position: absolute; left: 0; top: 0; width: 228px; height: 100%;
    background: var(--card-white);
  }
  .contact__portrait {
    position: absolute; left: 14px; top: 16px; width: 200px; height: 200px;
    background: radial-gradient(ellipse at 40% 40%, #c9c9c9 0%, #e4e4e4 55%, var(--card-white) 80%);
    border-radius: 4px;
  }
  .contact__wordmark {
    position: absolute; right: 14px; bottom: 30px;
    white-space: nowrap;
    font-size: 24px; font-weight: 300; color: var(--ink); letter-spacing: -0.3px;
  }
  .contact__dark-panel {
    position: absolute; left: 228px; top: 0; right: 0; bottom: 0;
    background: linear-gradient(160deg, var(--card-dark-edge) 0%, var(--card-dark) 60%);
  }
  .contact__names {
    position: absolute; left: 30px; top: 40px;
    font-size: 24px; color: var(--text-light); letter-spacing: -0.3px;
    white-space: nowrap;
  }
  .contact__list {
    position: absolute; right: 18px; bottom: 26px;
    list-style: none; text-align: right;
  }
  .contact__item {
    display: flex; align-items: center; justify-content: flex-end; gap: 10px;
    font-size: 14px; line-height: 21px; color: var(--text-light);
    white-space: nowrap;
  }
  .contact__icon { width: 11px; height: 11px; flex: none; }
  /* Name side */
  .card--names { left: 620px; background: var(--card-white); }
  .names__block {
    position: absolute; left: 120px; top: 104px; width: 320px;
  }
  .names__wordmark {
    text-align: right; padding-right: 6px;
    font-size: 32px; font-weight: 300; color: var(--ink); letter-spacing: -0.5px;
    white-space: nowrap; line-height: 44px;
  }
  .names__rule { height: 1px; background: var(--ink); }
  .names__people {
    padding-left: 40px; margin-top: 6px;
    font-family: "Kalam", cursive; font-size: 28px; color: var(--ink);
    white-space: nowrap;
  }
</style>
</head>
<body>
  <section class="card card--contact">
    <div class="contact__portrait-panel">
      <div class="contact__portrait" role="img" aria-label="Black and white line sketch of a woman with swept hair and red lips"></div>
      <p class="contact__wordmark">Thrive360onward</p>
    </div>
    <div class="contact__dark-panel">
      <p class="contact__names">Kim, Mavis &amp; Gwen</p>
      <ul class="contact__list">
        <li class="contact__item">0439615028
          <svg class="contact__icon" viewBox="0 0 12 12"><path d="M2 1h3l1 3-1.5 1a7 7 0 0 0 2.5 2.5L8 6l3 1v3c-5 1-10-4-9-9z" fill="var(--accent-red)"/></svg></li>
        <li class="contact__item">Thrive360onward@mailbox-example.net
          <svg class="contact__icon" viewBox="0 0 12 12"><rect x="0.5" y="2" width="11" height="8" fill="var(--accent-red)"/><path d="M1 2.5l5 4 5-4" stroke="var(--card-dark)" fill="none"/></svg></li>
        <li class="contact__item">Facebook/Thrive360onward
          <svg class="contact__icon" viewBox="0 0 12 12"><rect x="1" y="1" width="10" height="10" fill="var(--accent-red)"/></svg></li>
        <li class="contact__item">www.thrive360onward-example.com.au
          <svg class="contact__icon" viewBox="0 0 12 12"><circle cx="6" cy="6" r="5.5" fill="var(--accent-red)"/><path d="M0.5 6h11M6 0.5v11" stroke="var(--card-dark)" stroke-width="0.8"/></svg></li>
      </ul>
    </div>
  </section>

  <section class="card card--names">
    <div class="names__block">
      <p class="names__wordmark">Thrive360onward</p>
      <div class="names__rule"></div>
      <p class="names__people">Kim, Mavis &amp; Gwen</p>
    </div>
  </section>
</body>
</html>
```